Website for IT Security Company in Austria with small and medium business customer base

I own a one man IT security company with a customer small to medium business customer base and need a professional looking website that contains the following information:
- Home page: About the company....
- Services: The services that I offer. It would be nice to have icons if possible (e.g Directory Service icon, digital certificate icon, ...) but this is not a must have.
- About me
- Blog: This is not a must have. It would be ok to just link it to an external blog.
- Impressum
- Contact: No form, just telephone number and e-mail address
- Anything else that you think is necessary for a professional appearance
Also I attached the company design. I do have all source files for the logo if required.

Target Market(s)

Small and medium business of all branches located in Austria

Industry/Entity Type

Cyber Security

Coding

Coded - Design and coding required

Number of Pages Required

5+ page

Font styles to use
Serif
Sans Serif
Other font styles liked:
• Bitsumishi, Bankgothic

Colors

Designer to choose only greyscale colors for use in the design.

Requirements
Must have
• The website must be a mobile-first design.
The design should not be too colorful or playful.
The logo should be used as much as possible
Navigation bar with multi drop-down menu for the services that I offer.
Example:
Services
-> Implementations
-> Implementation Service A
-> Implementation Service B
-> Security Audit
-> Audit A
-> Audit B
Maybe you could have service cards that describe the services briefly and on click redirect to the site that describes the service in detail.
End of example
Logo
contact
impressum
services that I offer
about me
about the company
Nice to have
• Icons would be nice (e.g. house for homepage, letter for contact, ...)
Also for the services I offer icons would be nice (Directory Service, digtial certificates, hacking, security auditing)
For the fonts I have only sugested Bitsumishi and Bankgothic as they are part of my logo. No sure if you feel they make sense as part of the website
Should not have
• forms.
I want to the site to be made as easy as possible (HTML5, CSS, javascript/php/.net)
I do not want a wordpress template or suchlike.

```html
<!DOCTYPE html>
<html lang="en">
<head>
<meta charset="utf-8">
<title>Graphite Guard IT Security</title>
<link href="https://fonts.googleapis.com/css2?family=Audiowide&family=Michroma&family=Lato:wght@400;700&family=Roboto:wght@400;500;700&display=swap" rel="stylesheet">
<style>
:root{
  --black:#000;
  --ink:#111;
  --white:#fff;
  --orange:#ff7f00;
  --grey:#8a8a8a;
  --light:#e6e7ea;
  --navy:#0b1620;
  --date:#f2a23a;
}
*{margin:0;padding:0;box-sizing:border-box}
html,body{width:1200px;height:3723px;overflow:hidden;background:var(--black)}
body{position:relative;font-family:"Lato",sans-serif;color:var(--white)}
.abs{position:absolute}
.display{font-family:"Audiowide",sans-serif;text-transform:uppercase;letter-spacing:2px}
.wide{font-family:"Michroma",sans-serif;text-transform:uppercase}

/* header */
.site-header{left:0;top:0;width:1200px;height:148px;background:var(--black)}
.brand{left:111px;top:32px;width:210px;text-align:center}
.brand-mark{display:block;width:54px;height:40px;margin:0 auto 8px;border:5px solid var(--white);border-radius:4px}
.brand-name{font-family:"Michroma",sans-serif;font-size:17px;letter-spacing:1px;color:var(--white);display:block}
.brand-sub{font-family:"Michroma",sans-serif;font-size:7px;letter-spacing:8px;color:var(--white);display:block;margin-top:2px}
.call-bar{left:554px;top:0;width:536px;height:65px;background:var(--white);clip-path:polygon(0 0,100% 0,93% 100%,7% 100%)}
.call-icon{left:642px;top:10px;width:44px;height:44px;border-radius:50%;background:var(--ink)}
.call-text{left:702px;top:22px;font-family:"Michroma",sans-serif;font-size:13px;color:var(--ink)}
.call-text small{font-size:9px;text-transform:uppercase;margin-right:4px}
.main-nav{left:457px;top:97px;display:flex;font-family:"Michroma",sans-serif;font-size:10px;text-transform:uppercase}
.main-nav a{color:var(--white);text-decoration:none;position:absolute;white-space:nowrap}
.main-nav a.active::after{content:"";position:absolute;left:0;right:0;top:17px;height:2px;background:var(--white)}
.nav-divider{left:998px;top:90px;width:1px;height:26px;background:#888}

/* hero */
.hero{left:0;top:148px;width:1200px;height:684px;
  background:radial-gradient(ellipse at 50% 40%,#e9f4fb 0%,#9cc9e6 40%,#3b7fb0 75%,#1b3f5e 100%);
  clip-path:polygon(0 0,100% 0,100% 546px,983px 684px,217px 684px,0 546px)}
.hero-panel{left:192px;top:335px;width:816px;height:316px;background:rgba(0,0,0,.45)}
.hero-title{left:192px;top:372px;width:816px;text-align:center;font-size:46px;line-height:52px;color:var(--white)}
.btn-start{left:518px;top:500px;width:163px;height:47px;background:var(--orange);color:var(--white);font-family:"Michroma",sans-serif;font-size:11px;letter-spacing:2px;display:flex;align-items:center;justify-content:center;text-transform:uppercase}
.dot{top:754px;width:16px;height:16px;border-radius:50%;border:2px solid #fff;background:rgba(255,255,255,.4)}

/* about company */
.about-visual{left:104px;top:937px;width:457px;height:396px;
  background:linear-gradient(180deg,#2b6aa6,#14253a 45%,#4d5a66 70%,#1a1d22);
  clip-path:polygon(25% 0,75% 0,100% 50%,75% 100%,25% 100%,0 50%)}
.about-copy{left:600px;top:920px;width:495px;font-size:13.5px;line-height:21px}
.about-copy h2{font-size:25px;margin-bottom:14px;font-weight:400}
.about-copy h3{font-size:14px;margin:28px 0 18px;font-weight:400}
.about-copy p{margin-bottom:14px}

/* services */
.services-band{left:0;top:1434px;width:1200px;height:604px;background:var(--white);
  clip-path:polygon(217px 0,983px 0,1200px 123px,1200px 479px,983px 604px,217px 604px,0 479px,0 123px)}
.services-bg{left:0;top:1434px;width:1200px;height:604px;background:linear-gradient(180deg,#000,#0c1822)}
.section-title{width:1200px;left:0;text-align:center;font-size:30px;font-weight:400}
.service-card{top:1593px;width:313px;height:316px;text-align:center;color:var(--white);
  background:radial-gradient(ellipse at 50% 80%,#2a2a2a,#000 70%)}
.service-card.featured{background:var(--orange);box-shadow:0 6px 18px rgba(0,0,0,.35)}
.service-icon{position:absolute;left:84px;top:15px;width:144px;height:116px;background:var(--white);
  clip-path:polygon(25% 0,75% 0,100% 50%,75% 100%,25% 100%,0 50%)}
.service-icon svg{position:absolute;left:47px;top:33px}
.service-card h3{position:absolute;top:150px;width:100%;font-family:"Michroma",sans-serif;font-size:12px;letter-spacing:2px;font-weight:400;text-transform:uppercase}
.service-card .rule{position:absolute;left:141px;top:171px;width:30px;height:2px;background:var(--white)}
.service-card p{position:absolute;top:190px;left:20px;right:20px;font-size:12.5px;line-height:16px}
.service-card p+p{top:254px}

/* about me */
.aboutme-bg{left:0;top:2038px;width:1200px;height:557px;background:radial-gradient(ellipse at 80% 20%,#14324a,#050b12 70%)}
.aboutme-copy{left:110px;top:2124px;width:490px;font-size:13.5px;line-height:21px;text-align:justify}
.aboutme-copy h2{font-size:25px;font-weight:400;margin-bottom:14px}
.aboutme-copy p{margin-bottom:21px}
.cert-a{left:110px;top:2353px;width:140px;height:149px;background:var(--white)}
.cert-b{left:276px;top:2353px;width:237px;height:149px;background:#1a0f0a;border:6px solid #d2451f}
.portrait{left:625px;top:2133px;width:464px;height:369px;background:linear-gradient(180deg,#f3f3f3,#d9d0c6)}

/* blog */
.blog-bg{left:0;top:2595px;width:1200px;height:695px;background:linear-gradient(180deg,#0b1620,#15283a)}
.blog-band{left:0;top:2595px;width:1200px;height:695px;background:var(--light);
  clip-path:polygon(217px 0,983px 0,1200px 123px,1200px 572px,983px 695px,217px 695px,0 572px,0 123px)}
.blog-title{top:2680px;color:var(--ink)}
.post{top:2756px;width:311px;font-family:"Roboto",sans-serif}
.post-media{width:311px;height:198px}
.post-date{margin-top:18px;font-size:12px;color:var(--date)}
.post h3{margin-top:10px;font-size:20px;font-weight:500;color:var(--ink)}
.post p{margin-top:10px;font-size:13px;line-height:25px;color:var(--grey);height:50px;overflow:hidden}
.btn-more{display:inline-flex;align-items:center;gap:5px;margin-top:15px;width:157px;height:47px;justify-content:center;background:var(--ink);color:var(--white);font-size:13px;font-weight:700}
.carousel-arrow{top:2937px;width:40px;height:40px;border-radius:50%;background:var(--black);display:flex;align-items:center;justify-content:center}

/* footer */
.site-footer{left:0;top:3290px;width:1200px;height:433px;background:radial-gradient(ellipse at 30% 30%,#0f2233,#02070c 70%)}
.footer-brand{left:120px;top:3386px;width:280px;text-align:center}
.footer-brand .brand-mark{width:70px;height:52px}
.footer-brand .brand-name{font-size:21px}
.footer-brand .brand-sub{font-size:8px;letter-spacing:10px}
.social{top:3528px;width:32px;height:32px;border-radius:50%;border:2px solid var(--white)}
.footer-col{top:3381px;font-size:14.5px;line-height:28px}
.footer-col h4{font-family:"Michroma",sans-serif;font-size:14px;letter-spacing:2px;font-weight:400;text-transform:uppercase;margin-bottom:12px}
.footer-col a{display:block;color:var(--white);text-decoration:none}
.contact-item{left:889px;font-size:14.5px;line-height:20px}
.footer-rule{left:98px;top:3630px;width:1004px;height:1px;background:#333}
.copyright{left:0;width:1200px;top:3664px;text-align:center;font-size:14.5px}
</style>
</head>
<body>

<header class="abs site-header">
  <div class="abs brand">
    <span class="brand-mark"></span>
    <span class="brand-name">Graphite Guard</span>
    <span class="brand-sub">IT Security</span>
  </div>
  <div class="abs call-bar"></div>
  <div class="abs call-icon">
    <svg width="44" height="44" viewBox="0 0 44 44"><path d="M16 13c1-1 2-1 3 0l2 3c1 1 0 2-1 3 1 2 3 4 5 5 1-1 2-2 3-1l3 2c1 1 1 2 0 3l-2 2c-6 0-15-9-15-15z" fill="#fff"/></svg>
  </div>
  <div class="abs call-text"><small>Call us today :</small>+43 660 11223344</div>
  <nav class="abs main-nav">
    <a class="active" style="left:0">Home</a>
    <a style="left:68px">Services</a>
    <a style="left:165px">About me</a>
    <a style="left:269px">Blog</a>
    <a style="left:335px">Impressum</a>
    <a style="left:447px">Contact</a>
    <a style="left:567px">&#9786;&nbsp;Log in</a>
  </nav>
  <div class="abs nav-divider"></div>
</header>

<section class="abs hero" role="img" aria-label="Glowing blue digital security scene with monitors and padlocks"></section>
<div class="abs hero-panel"></div>
<h1 class="abs hero-title display">We are a one man IT<br>security company</h1>
<a class="abs btn-start">Get started</a>
<span class="abs dot" style="left:570px"></span>
<span class="abs dot" style="left:592px"></span>
<span class="abs dot" style="left:614px"></span>

<section>
  <div class="abs about-visual" role="img" aria-label="Hexagon collage of server rooms and IT specialists at work"></div>
  <div class="abs about-copy">
    <h2 class="display">About Graphite Guard</h2>
    <p>Cyber security incidents are unfortunately no longer a rarity , but rather commonplace.</p>
    <p>In many cases, increasing IT security could be quite easy.</p>
    <p>I am happy to support you with my profound practice and years of experience.</p>
    <h3 class="display">Why Graphite Guard?</h3>
    <p>In the best case scenario, IT security should cost as few of your valuable resources as possible. With my help, you do not have to lift a heavy oak shield in the figurative sense, but only use an incomparably lighter but equally hard one made of graphite. So you can continue to put your strength into your work.</p>
    <p style="margin-top:21px">With my 20 years of experience with a wide variety of company types and sizes from a handful to several thousand employees worldwide, I can offer you top-level security know-how. This enables me to carry out both security checks and the necessary safeguards in professional quality.</p>
  </div>
</section>

<section>
  <div class="abs services-bg"></div>
  <div class="abs services-band"></div>
  <h2 class="abs section-title display" style="top:1516px;color:var(--ink)">Services we offer</h2>

  <article class="abs service-card" style="left:111px">
    <div class="service-icon"><svg width="50" height="50" viewBox="0 0 50 50" fill="none" stroke="#111" stroke-width="2"><circle cx="14" cy="10" r="5"/><path d="M6 44V24c0-4 4-6 8-6s8 2 8 6v20"/><circle cx="32" cy="26" r="10"/><path d="M28 30v-4M32 30v-8M36 30v-6"/><circle cx="42" cy="42" r="5"/></svg></div>
    <h3>Implementations</h3><span class="rule"></span>
    <p>Meridian PKI<br>Meridian tiering infrastructure</p>
  </article>

  <article class="abs service-card featured" style="left:444px">
    <div class="service-icon"><svg width="50" height="50" viewBox="0 0 50 50" fill="none" stroke="#111" stroke-width="2"><path d="M25 4l12 5v9c0 8-6 13-12 15-6-2-12-7-12-15V9z"/><path d="M19 18l4 4 8-8"/><path d="M4 38h8l10 4h12l10-6M4 34v12"/></svg></div>
    <h3>Security check</h3><span class="rule"></span>
    <p>The purpose of the security checks is to check the vulnerability of your systems</p>
    <p>Directory Service<br>Directory Service password verification<br>Public Key Infrastructure (PKI)</p>
  </article>

  <article class="abs service-card" style="left:776px">
    <div class="service-icon"><svg width="50" height="50" viewBox="0 0 50 50" fill="none" stroke="#111" stroke-width="2"><circle cx="22" cy="22" r="16" stroke-dasharray="6 3"/><circle cx="22" cy="22" r="9"/><circle cx="30" cy="30" r="7"/><path d="M35 35l9 9"/></svg></div>
    <h3>Security optimization</h3><span class="rule"></span>
    <p>The purpose of security optimization is to harden your systems against attacks</p>
    <p>Meridian OS operating system hardening<br>Optimization of Meridian Cloud Identities</p>
  </article>
</section>

<section>
  <div class="abs aboutme-bg"></div>
  <div class="abs aboutme-copy">
    <h2 class="display">About me</h2>
    <p>In my almost 20 years of experience as an IT administrator, trainer, consultant and solution architect, I have been able to work for many companies in different industries and sizes.</p>
    <p>IT security, especially in the Meridian environment, has emerged as my greatest passion. Since then I have been supporting companies in realizing their security requirements.</p>
  </div>
  <div class="abs cert-a" role="img" aria-label="Ethical hacker certification badge"></div>
  <div class="abs cert-b" role="img" aria-label="Certified security master certificate"></div>
  <div class="abs portrait" role="img" aria-label="Portrait photo of the company owner"></div>
</section>

<section>
  <div class="abs blog-bg"></div>
  <div class="abs blog-band"></div>
  <h2 class="abs section-title display blog-title">Latest blog posts</h2>

  <article class="abs post" style="left:111px">
    <div class="post-media" role="img" aria-label="Hand drawing cloud and device icons" style="background:linear-gradient(135deg,#06121a,#1d5a60 60%,#9fd2c4)"></div>
    <div class="post-date">&#9633; Jan 30th 2021</div>
    <h3>Back to basics</h3>
    <p>Die Auswertung von 67529 öffentlich gemeldeten Security Vorfällen (die Dunkelziffer</p>
    <a class="btn-more">LEARN MORE &#10148;</a>
  </article>

  <article class="abs post" style="left:444px">
    <div class="post-media" role="img" aria-label="Tablet with security icons overlay" style="background:linear-gradient(135deg,#c9ccd0,#8e959c)"></div>
    <div class="post-date">&#9633; Jan 18th 2021</div>
    <h3>Possible to protect against</h3>
    <p>On Meridian OS systems there are different places where passwords or their</p>
    <a class="btn-more">LEARN MORE &#10148;</a>
  </article>

  <article class="abs post" style="left:778px">
    <div class="post-media" role="img" aria-label="Security analyst at a desk with monitors" style="background:linear-gradient(135deg,#0e1f33,#2f5f8a 60%,#1a2430)"></div>
    <div class="post-date">&#9633; Jan 12th 2021</div>
    <h3>Ransomware prevention</h3>
    <p>Since I have been able to support companies several times in the last few months, the</p>
    <a class="btn-more">LEARN MORE &#10148;</a>
  </article>

  <span class="abs carousel-arrow" style="left:31px"><svg width="12" height="14" viewBox="0 0 12 14"><path d="M9 1L3 7l6 6" stroke="#fff" stroke-width="2" fill="none"/></svg></span>
  <span class="abs carousel-arrow" style="left:1125px"><svg width="12" height="14" viewBox="0 0 12 14"><path d="M3 1l6 6-6 6" stroke="#fff" stroke-width="2" fill="none"/></svg></span>
</section>

<footer class="abs site-footer"></footer>
<div class="abs footer-brand">
  <span class="brand-mark"></span>
  <span class="brand-name">Graphite Guard</span>
  <span class="brand-sub">IT Security</span>
</div>
<span class="abs social" style="left:172px" aria-label="Social profile"></span>
<span class="abs social" style="left:215px" aria-label="Social profile"></span>
<span class="abs social" style="left:257px" aria-label="Social profile"></span>
<span class="abs social" style="left:301px" aria-label="Social profile"></span>

<nav class="abs footer-col" style="left:444px">
  <h4>Quick links</h4>
  <a>Home</a><a>About us</a><a>Services</a><a>About me</a><a>Blog</a><a>Contact</a>
</nav>
<nav class="abs footer-col" style="left:635px">
  <h4>Information</h4>
  <a>Support</a><a>Blog</a><a>Privacy policy</a><a>Terms condition</a>
</nav>
<div class="abs footer-col" style="left:856px"><h4>Conact us</h4></div>
<svg class="abs" style="left:852px;top:3430px" width="20" height="20" viewBox="0 0 20 20"><path d="M4 2c1-1 2-1 3 0l2 3c0 1 0 2-1 2 1 3 3 5 5 6 1-1 2-1 3 0l2 2c1 1 0 2-1 3-8 0-15-7-13-16z" fill="#fff"/></svg>
<div class="abs contact-item" style="top:3429px">Phone:<br>+43 660 11223344</div>
<svg class="abs" style="left:852px;top:3487px" width="20" height="16" viewBox="0 0 20 16"><rect x="1" y="1" width="18" height="14" fill="#fff"/><path d="M1 1l9 7 9-7" stroke="#0b1620" stroke-width="1.5" fill="none"/></svg>
<div class="abs contact-item" style="top:3482px">Email:<br>office@graphiteguard.at</div>
<div class="abs footer-rule"></div>
<p class="abs copyright">© 2020 Company name | All Rights Reserved | Disclaimer</p>

</body>
</html>
```